Ledgerwise Forge - WordPress Theme & Logo

Design a logo and Wordpress website design for Ledgerwise Forge. Ledgerwise Forge provides cryptocurrency development services to clients who need a team to create & continue developing a new cryptocurrency or who want to replace their current cryptocurrency development team. more details in the attached document.
Updates

Target Market(s)

Entrepreneurs who are building a business / platform that makes use of an underlying cryptocurrency.

Logo Text

LF or Ledgerwise Forge

Coding

Coded - Design and coding required

Font styles to use
Sans Serif

Requirements
Must have
• Professional logo, complete coded Wordpress theme for all pages, containing all specified links and buttons
Nice to have
• It would be nice if the buttons that are meant to integrate with Dealtrail contain the necessary code for that. I can provide any necessary Dealtrail details from my account.
Should not have
• Slow loading time

```html
<!DOCTYPE html>
<html lang="en">
<head>
<meta charset="utf-8">
<title>Ledgerwise Forge – Home Page Concepts</title>
<link rel="stylesheet" href="https://fonts.googleapis.com/css2?family=Montserrat:wght@600;700&family=Roboto:wght@400;500;700&display=swap">
<style>
:root{
  --stage:#dcdcdc;
  --white:#ffffff;
  --ink:#2b2b2b;
  --muted:#6b6b6b;
  --blue:#1565c0;
  --blue-bright:#1e7be0;
  --navy:#0d2a78;
  --navy-deep:#0a1f5c;
  --ice:#ecf3fb;
  --foot:#f4f4f4;
  --dark-icon:#3a3a3a;
  --star:#f5c518;
}
*{box-sizing:border-box;margin:0;padding:0}
html,body{width:719px;height:1200px;overflow:hidden;background:var(--stage)}
.stage{position:absolute;left:0;top:0;width:1484px;height:2480px;transform:scale(.4845);transform-origin:0 0;background:var(--stage)}
.page{position:absolute;top:52px;width:650px;height:2375px;background:var(--white);font-family:"Roboto",sans-serif;color:var(--ink);overflow:hidden;box-shadow:0 0 6px rgba(0,0,0,.12)}
.page--a{left:64px}
.page--b{left:771px}
.page>section,.page>header,.page>footer{position:absolute;left:0;width:650px}

/* nav */
.site-nav{top:0;height:44px;background:var(--white);border-top:2px solid var(--blue)}
.brand{position:absolute;left:60px;top:9px;display:flex;align-items:center;gap:6px}
.brand__mark{width:26px;height:26px;background:var(--blue);display:block}
.brand__name{font-family:"Montserrat",sans-serif;font-weight:700;font-size:7.5px;line-height:8.5px;color:var(--navy-deep);text-transform:uppercase}
.nav-links{position:absolute;left:173px;top:17px;display:flex;gap:12px;font-size:7.6px;color:var(--ink)}
.nav-links .is-current{color:var(--blue)}
.btn{display:inline-block;border-radius:14px;font-family:"Roboto",sans-serif;font-weight:700;text-transform:uppercase;text-align:center;color:var(--white);background:linear-gradient(180deg,var(--blue-bright),var(--navy));white-space:nowrap}
.nav-cta{position:absolute;left:466px;top:9px;width:123px;height:26px;line-height:26px;font-size:7px;font-weight:500}

/* hero */
.hero{top:44px;height:366px;overflow:hidden}
.hero__image{position:absolute;inset:0}
.hero--coin .hero__image{background:radial-gradient(circle at 73% 66%,#b98a3c 0,#6a4a1f 14%,rgba(20,30,80,0) 28%),radial-gradient(circle at 8% 55%,#6a5a3a 0,rgba(0,0,0,0) 22%),linear-gradient(160deg,#0a1a4a 0%,#07183f 45%,#1a3f8e 100%)}
.hero--laptop .hero__image{background:radial-gradient(circle at 30% 30%,#2fa2c7 0,rgba(20,90,140,0) 35%),radial-gradient(circle at 75% 55%,#d8a88f 0,rgba(0,0,0,0) 22%),linear-gradient(150deg,#0d3b63 0%,#1a6d9a 45%,#8fa3b5 100%)}
.hero__curve{position:absolute;left:0;bottom:0;width:650px;height:90px}
.hero__title{position:absolute;font-family:"Montserrat",sans-serif;font-weight:700;font-size:14px;line-height:20px;color:var(--white);text-transform:uppercase}
.hero--coin .hero__title{left:59px;top:116px;width:360px}
.hero--laptop .hero__title{left:130px;top:140px;width:390px;text-align:center}
.hero__btn{position:absolute;height:26px;line-height:26px;font-size:7px;padding:0 14px}
.hero--coin .hero__btn{left:59px;top:173px}
.hero--laptop .hero__btn{left:268px;top:196px}

/* shared headings */
.section-title{font-family:"Montserrat",sans-serif;font-weight:700;font-size:14.5px;text-transform:uppercase;text-align:center;color:var(--ink)}
.section-title::after{content:"";display:block;width:80px;height:2px;background:var(--blue);margin:6px auto 0}
.section-title--light{color:var(--white)}
.section-title--light::after{background:var(--white)}

/* welcome */
.welcome{top:408px;height:142px;background:var(--ice)}
.welcome .section-title{position:absolute;top:34px;width:100%}
.welcome__text{position:absolute;left:105px;top:80px;width:440px;font-size:7.4px;line-height:14px;text-align:center;color:var(--muted)}

/* about */
.about{top:550px;height:342px;background:var(--white)}
.about__ring{position:absolute;left:60px;top:53px;width:246px;height:240px;border-radius:50%;border-left:4px solid var(--blue);border-bottom:2px solid var(--blue)}
.about__photo{position:absolute;left:70px;top:55px;width:236px;height:236px;border-radius:50%;background:radial-gradient(circle at 68% 38%,#3a78c8 0,#14306a 30%,rgba(0,0,0,0) 45%),linear-gradient(135deg,#d9c9b8 0%,#a68a72 40%,#e9e6e2 100%)}
.about__title{position:absolute;left:332px;top:128px;font-family:"Montserrat",sans-serif;font-weight:700;font-size:17px;color:var(--ink);display:flex;align-items:center;gap:8px}
.about__title::after{content:"";width:50px;height:2px;background:var(--blue)}
.about__text{position:absolute;left:332px;top:160px;width:258px;font-size:7px;line-height:13px;text-align:justify;color:var(--muted)}
.about__text p+p{margin-top:7px}
.about__btn{position:absolute;left:332px;top:287px;width:78px;height:25px;line-height:25px;font-size:7.4px}

/* services */
.services{top:892px;height:314px;background:radial-gradient(ellipse at 50% 70%,#1d63c4 0,rgba(20,70,170,0) 60%),linear-gradient(180deg,#0c2470 0%,#0f3d9c 100%)}
.services .section-title{position:absolute;top:34px;width:100%}
.service-cards{position:absolute;left:60px;top:87px;display:flex;gap:8px}
.service-card{width:171px;height:191px;background:var(--white);border-radius:3px;padding:14px 8px 0}
.service-card__icon{width:50px;height:46px;display:block}
.service-card__title{font-size:9.2px;font-weight:500;margin:12px 0 7px;color:var(--ink)}
.ticks{list-style:none}
.ticks li{position:relative;padding-left:15px;font-size:6.8px;line-height:9.4px;color:var(--muted);margin-bottom:3px}
.ticks li::before{content:"✓";position:absolute;left:1px;top:1px;width:7px;height:7px;border:1px solid var(--blue);border-radius:50%;font-size:5px;line-height:6px;text-align:center;color:var(--blue)}

/* offerings */
.offerings{top:1206px;height:220px;background:var(--white)}
.offerings .section-title{position:absolute;top:44px;width:100%}
.timeline{position:absolute;left:60px;top:148px;width:530px;height:1px;background:var(--blue)}
.offer{position:absolute;top:92px;width:130px;margin-left:-65px;text-align:center}
.offer__icon{width:38px;height:38px;margin:0 auto;border-radius:50%;background:var(--blue);border:3px solid #cfe0f5;display:flex;align-items:center;justify-content:center}
.offer__dot{width:11px;height:11px;border-radius:50%;background:var(--blue);margin:11px auto 0;border:2px solid var(--white);box-shadow:0 0 0 1px var(--blue)}
.offer__label{font-size:7.4px;color:var(--muted);margin-top:6px}

/* why */
.why{top:1426px;height:277px;background:var(--ice)}
.why .section-title{position:absolute;top:33px;width:100%}
.why-cards{position:absolute;left:60px;top:79px;display:flex;gap:10px}
.why-card{width:169px;height:165px;background:var(--white);border-radius:8px;text-align:center;padding-top:20px}
.why-card--featured{box-shadow:0 2px 10px rgba(0,40,120,.18);border-bottom:3px solid var(--blue)}
.why-card__icon{width:56px;height:56px;border-radius:50%;background:var(--dark-icon);margin:0 auto;display:flex;align-items:center;justify-content:center}
.why-card--featured .why-card__icon{background:linear-gradient(180deg,var(--blue-bright),var(--navy))}
.why-card__title{font-family:"Montserrat",sans-serif;font-weight:700;font-size:10.5px;margin:18px 0 8px;color:var(--ink)}
.why-card__text{font-size:7.6px;line-height:13px;color:var(--muted);padding:0 14px}

/* testimonials */
.testimonials{top:1703px;height:283px;background:var(--white)}
.testimonials .section-title{position:absolute;top:50px;width:100%}
.quote-cards{position:absolute;left:60px;top:165px;display:flex;gap:6px}
.quote-card{position:relative;width:172px;height:120px;border:1px solid #e3e8ef;border-top:2px solid var(--blue);border-radius:10px 10px 6px 6px;text-align:center;padding-top:28px}
.quote-card__badge{position:absolute;left:66px;top:-20px;width:38px;height:38px;border-radius:50%;background:var(--white);border:2px solid var(--blue)}
.quote-card__badge::after{content:"";position:absolute;left:9px;top:9px;width:16px;height:16px;border-radius:50%;background:#cfe0f5}
.quote-card__name{font-size:9.4px;font-weight:500;color:var(--ink)}
.stars{color:var(--star);font-size:6px;letter-spacing:1px;margin:1px 0 7px}
.quote-card__text{font-size:7px;line-height:13.5px;color:var(--muted);padding:0 6px}

/* cta */
.cta{top:1986px;height:270px;background:linear-gradient(160deg,#123c99 0%,#1758c4 55%,#2a7ae0 100%)}
.cta .section-title{position:absolute;top:24px;width:100%}
.cta__text{position:absolute;left:88px;top:63px;width:474px;font-size:7.4px;line-height:14px;text-align:center;color:var(--white)}
.cta__btn{position:absolute;left:286px;top:120px;width:78px;height:25px;line-height:25px;font-size:7.4px;color:var(--blue);background:var(--white)}
.cta__curve{position:absolute;left:0;bottom:0;width:650px;height:90px}

/* footer */
.site-footer{top:2236px;height:139px;background:var(--foot)}
.site-footer .brand{left:62px;top:3px}
.socials{position:absolute;left:78px;top:56px;display:flex;gap:3px}
.socials span{width:19px;height:19px;border-radius:50%;border:1px solid var(--blue);background:var(--white);position:relative}
.socials span:first-child{background:var(--blue)}
.foot-col{position:absolute;top:0}
.foot-col h4{font-size:8.6px;font-weight:400;color:var(--ink);margin-bottom:6px}
.foot-col h4::after{content:"";display:block;width:26px;height:1.5px;background:var(--blue);margin-top:3px}
.foot-col ul{list-style:none}
.foot-col li{font-size:7.2px;line-height:13.4px;color:var(--ink);padding-left:16px;position:relative}
.foot-col li::before{content:"";position:absolute;left:2px;top:4px;width:4px;height:4px;border:1px solid var(--blue);border-radius:50%}
.foot-col--quick{left:207px}
.foot-col--about{left:299px}
.foot-col--news{left:422px}
.newsletter{width:166px;height:24px;border:1px solid #d8dde4;border-radius:12px;background:var(--white);position:relative;font-size:6.8px;color:var(--muted);line-height:22px;padding-left:9px;margin-top:3px}
.newsletter__send{position:absolute;right:3px;top:2px;width:18px;height:18px;border-radius:50%;background:var(--blue);display:flex;align-items:center;justify-content:center}
.copyright{position:absolute;left:0;width:100%;top:174px;text-align:center;font-size:6.6px;color:var(--ink)}
.footer-rule{position:absolute;left:60px;top:164px;width:530px;height:1px;background:#e0e0e0}
</style>
</head>
<body>
<div class="stage">

<!-- Concept A -->
<div class="page page--a">
  <header class="site-nav">
    <div class="brand"><span class="brand__mark"></span><span class="brand__name">Ledgerwise<br>Forge</span></div>
    <nav class="nav-links"><span class="is-current">Home</span><span>About Us</span><span>Services</span><span>Our Methods</span><span>Testimonials</span><span>Blog</span></nav>
    <span class="btn nav-cta">Schedule Consultation</span>
  </header>
  <section class="hero hero--coin">
    <div class="hero__image" role="img" aria-label="Dark blue digital network background with a glowing gold coin"></div>
    <h1 class="hero__title">Your own cryptocurrency. Secure, easy to use, and built by an expert team.</h1>
    <span class="btn hero__btn">Download Free PDF</span>
    <svg class="hero__curve" viewBox="0 0 650 90" preserveAspectRatio="none"><path d="M0,0 Q325,150 650,0 L650,90 L0,90Z" fill="#ecf3fb"/><path d="M0,0 Q325,150 650,0" fill="none" stroke="#1565c0" stroke-width="3"/></svg>
  </section>
  <section class="welcome">
    <h2 class="section-title">Welcome to Ledgerwise Forge</h2>
    <p class="welcome__text">Ledgerwise Forge adds professionalism to cryptocurrency development. Our done-for-you service covers everything from development and IT operations to ongoing support. You have access to a full team, for less than the typical cost of a single developer.</p>
  </section>
  <section class="about">
    <div class="about__ring"></div>
    <div class="about__photo" role="img" aria-label="Developer working at a desk with a trading chart on screen"></div>
    <h2 class="about__title">ABOUT ME</h2>
    <div class="about__text">
      <p>Ledgerwise Forge provides a complete service that handles the development, IT operations and support for your cryptocurrency. Cryptocurrency development can be difficult and complex, and a quality development team is hard to find and expensive.</p>
      <p>Ledgerwise Forge has an experienced team that has helped several clients launch and enhance their cryptocurrencies, including successfully running the Vantor cryptocurrency since 2017, and writing a next-generation cryptocurrency from scratch.</p>
    </div>
    <span class="btn about__btn">Read More</span>
  </section>
  <section class="services">
    <h2 class="section-title section-title--light">Our Services</h2>
    <div class="service-cards">
      <article class="service-card">
        <svg class="service-card__icon" viewBox="0 0 50 46" fill="none" stroke="#333" stroke-width="1.3"><circle cx="25" cy="23" r="20" stroke-dasharray="4 3"/><path d="M25 12 L35 17 L35 28 L25 33 L15 28 L15 17Z M15 17 L25 22 L35 17 M25 22 L25 33" stroke="#1565c0"/></svg>
        <h3 class="service-card__title">Blockchain Creation &amp; Launch</h3>
        <ul class="ticks"><li>Base fixed price for cryptocurrency development &amp; launch–would be customizable based on client requirements</li></ul>
      </article>
      <article class="service-card">
        <svg class="service-card__icon" viewBox="0 0 50 46" fill="none" stroke="#333" stroke-width="1.3"><circle cx="25" cy="23" r="7" stroke="#1565c0"/><path d="M4 8 H14 L18 16 M46 8 H36 L32 16 M4 38 H14 L18 30 M46 38 H36 L32 30 M2 23 H18 M32 23 H48"/><circle cx="4" cy="8" r="2"/><circle cx="46" cy="8" r="2"/><circle cx="4" cy="38" r="2"/><circle cx="46" cy="38" r="2"/></svg>
        <h3 class="service-card__title">Basic offering</h3>
        <ul class="ticks"><li>Lower cost per month</li><li>Slower release schedule (about every 3 months)</li><li>Client assists with testing new releases</li><li>Less input into future roadmap/features</li><li>Limited support hours/priority (always available for emergencies)</li></ul>
      </article>
      <article class="service-card">
        <svg class="service-card__icon" viewBox="0 0 50 46" fill="none" stroke="#333" stroke-width="1.3"><rect x="3" y="2" width="20" height="40" rx="3"/><rect x="14" y="12" width="22" height="22" rx="2" stroke="#1565c0"/><path d="M25 16 L31 19 L31 26 L25 29 L19 26 L19 19Z" stroke="#1565c0"/></svg>
        <h3 class="service-card__title">Full service offering</h3>
        <ul class="ticks"><li>Mid-range cost per month</li><li>Releases every 1.5 - 2 months</li><li>Client can help request/prioritize new features</li><li>Full testing by my team prior to release</li><li>Priority support during normal business hours, always available for emergencies</li></ul>
      </article>
    </div>
  </section>
  <section class="offerings">
    <h2 class="section-title">Our Offerings</h2>
    <div class="timeline"></div>
    <div class="offer" style="left:139px"><div class="offer__icon"><svg width="18" height="18" viewBox="0 0 18 18" fill="none" stroke="#fff" stroke-width="1.2"><path d="M9 2 L15 5.5 L15 12.5 L9 16 L3 12.5 L3 5.5Z M3 5.5 L9 9 L15 5.5 M9 9 V16"/></svg></div><div class="offer__dot"></div><div class="offer__label">Blockchain Creation &amp; Launch</div></div>
    <div class="offer" style="left:272px"><div class="offer__icon"><svg width="18" height="18" viewBox="0 0 18 18" fill="none" stroke="#fff" stroke-width="1.2"><rect x="2" y="3" width="14" height="9" rx="1"/><path d="M6 15 H12 M9 12 V15"/></svg></div><div class="offer__dot"></div><div class="offer__label">Blockchain Development</div></div>
    <div class="offer" style="left:399px"><div class="offer__icon"><svg width="18" height="18" viewBox="0 0 18 18" fill="none" stroke="#fff" stroke-width="1.2"><rect x="2" y="2" width="6" height="6"/><rect x="10" y="2" width="6" height="6"/><rect x="2" y="10" width="6" height="6"/><rect x="10" y="10" width="6" height="6"/></svg></div><div class="offer__dot"></div><div class="offer__label">Blockchain Operations</div></div>
    <div class="offer" style="left:511px"><div class="offer__icon"><svg width="18" height="18" viewBox="0 0 18 18" fill="none" stroke="#fff" stroke-width="1.2"><rect x="2" y="2" width="14" height="14" rx="2"/><circle cx="9" cy="10" r="3"/><path d="M2 5 H16"/></svg></div><div class="offer__dot"></div><div class="offer__label">Blockchain Support</div></div>
  </section>
  <section class="why">
    <h2 class="section-title">Why Choose Us</h2>
    <div class="why-cards">
      <article class="why-card"><div class="why-card__icon"><svg width="26" height="22" viewBox="0 0 26 22" fill="none" stroke="#fff" stroke-width="1.3"><path d="M9 3 H17 L20 7 L13 13 L6 7Z"/><path d="M1 16 H7 L13 18 L23 14"/></svg></div><h3 class="why-card__title">VALUE</h3><p class="why-card__text">A team of experts, regular updates, and fixed costs</p></article>
      <article class="why-card why-card--featured"><div class="why-card__icon"><svg width="24" height="24" viewBox="0 0 24 24" fill="none" stroke="#fff" stroke-width="1.3"><circle cx="12" cy="9" r="5"/><path d="M4 22 C4 16 20 16 20 22 M5 9 A7 7 0 0 1 19 9"/></svg></div><h3 class="why-card__title">SUPPORT</h3><p class="why-card__text">Receive advice and other services, beyond development.</p></article>
      <article class="why-card"><div class="why-card__icon"><svg width="20" height="24" viewBox="0 0 20 24" fill="none" stroke="#fff" stroke-width="1.3"><rect x="2" y="2" width="16" height="20" rx="1"/><path d="M6 7 H14 M6 11 H14 M8 15 H12"/></svg></div><h3 class="why-card__title">COMMITMENT</h3><p class="why-card__text">Enjoy regular updates and new features.</p></article>
    </div>
  </section>
  <section class="testimonials">
    <h2 class="section-title">Client Testimonials</h2>
    <div class="quote-cards">
      <article class="quote-card"><span class="quote-card__badge"></span><h3 class="quote-card__name">Lorum Ipsum Dolor</h3><div class="stars">★★★★★</div><p class="quote-card__text">Lorem ipsum dolor sit amet, consectetur adipiscing elit, sed do eiusmod tempor incididunt labore et dolore magna aliquaudet enimad minim veniam quis.</p></article>
      <article class="quote-card"><span class="quote-card__badge"></span><h3 class="quote-card__name">Lorum Ipsum Dolor</h3><div class="stars">★★★★★</div><p class="quote-card__text">Lorem ipsum dolor sit amet, consectetur adipiscing elit, sed do eiusmod tempor incididunt labore et dolore magna aliquaudet enimad minim veniam quis.</p></article>
      <article class="quote-card"><span class="quote-card__badge"></span><h3 class="quote-card__name">Lorum Ipsum Dolor</h3><div class="stars">★★★★★</div><p class="quote-card__text">Lorem ipsum dolor sit amet, consectetur adipiscing elit, sed do eiusmod tempor incididunt labore et dolore magna aliquaudet enimad minim veniam quis.</p></article>
    </div>
  </section>
  <section class="cta">
    <h2 class="section-title section-title--light">Schedule a Free Consultation</h2>
    <p class="cta__text">Lorem ipsum dolor sit amet, consectetur adipiscing elit, sed do eiusmod tempor incididunt ut labore et dolore magna aliqua. Ut enim ad minim veniam, quis nostrud exercitation ullamco laboris nisi ut aliquip ex ea commodo consequat. Duis aute irure dolor in reprehenderit in voluptate velit esse cillum dolore eu fugiat nulla pariatur excepteur.</p>
    <span class="btn cta__btn">Get Started</span>
    <svg class="cta__curve" viewBox="0 0 650 90" preserveAspectRatio="none"><path d="M0,90 Q325,-50 650,90Z" fill="#f4f4f4"/></svg>
  </section>
  <footer class="site-footer">
    <div class="brand"><span class="brand__mark"></span><span class="brand__name">Ledgerwise<br>Forge</span></div>
    <div class="socials"><span></span><span></span><span></span><span></span></div>
    <div class="foot-col foot-col--quick"><h4>Quick Links</h4><ul><li>Home</li><li>About Us</li><li>Our Services</li><li>Our Methods</li><li>Contact Us</li></ul></div>
    <div class="foot-col foot-col--about"><h4>About Links</h4><ul><li>Blog</li><li>Search</li><li>Privacy Policy</li><li>Terms Of Conditions</li></ul></div>
    <div class="foot-col foot-col--news"><h4>Get Our Newsletter</h4><div class="newsletter">Enter Email Address<span class="newsletter__send"><svg width="9" height="9" viewBox="0 0 10 10"><path d="M1 5 L9 1 L6 9 L5 6Z" fill="#fff"/></svg></span></div></div>
    <div class="footer-rule"></div>
    <p class="copyright">Copyrights 2021 LEDGERWISE FORGE. All Rights Reserved</p>
  </footer>
</div>

<!-- Concept B -->
<div class="page page--b">
  <header class="site-nav">
    <div class="brand"><span class="brand__mark"></span><span class="brand__name">Ledgerwise<br>Forge</span></div>
    <nav class="nav-links"><span class="is-current">Home</span><span>About Us</span><span>Services</span><span>Our Methods</span><span>Testimonials</span><span>Blog</span></nav>
    <span class="btn nav-cta">Schedule Consultation</span>
  </header>
  <section class="hero hero--laptop">
    <div class="hero__image" role="img" aria-label="Laptop showing a security padlock graphic while a person uses a phone"></div>
    <h1 class="hero__title">Your own cryptocurrency. Secure, easy to use, and built by an expert team.</h1>
    <span class="btn hero__btn">Download a Free PDF</span>
    <svg class="hero__curve" viewBox="0 0 650 90" preserveAspectRatio="none"><path d="M0,0 Q325,150 650,0 L650,90 L0,90Z" fill="#ecf3fb"/><path d="M0,0 Q325,150 650,0" fill="none" stroke="#1565c0" stroke-width="3"/></svg>
  </section>
  <section class="welcome">
    <h2 class="section-title">Welcome to Ledgerwise Forge</h2>
    <p class="welcome__text">Ledgerwise Forge adds professionalism to cryptocurrency development. Our done-for-you service covers everything from development and IT operations to ongoing support. You have access to a full team, for less than the typical cost of a single developer.</p>
  </section>
  <section class="about">
    <div class="about__ring"></div>
    <div class="about__photo" role="img" aria-label="Developer working at a desk with a trading chart on screen"></div>
    <h2 class="about__title">ABOUT ME</h2>
    <div class="about__text">
      <p>Ledgerwise Forge provides a complete service that handles the development, IT operations and support for your cryptocurrency. Cryptocurrency development can be difficult and complex, and a quality development team is hard to find and expensive.</p>
      <p>Ledgerwise Forge has an experienced team that has helped several clients launch and enhance their cryptocurrencies, including successfully running the Vantor cryptocurrency since 2017, and writing a next-generation cryptocurrency from scratch.</p>
    </div>
    <span class="btn about__btn">Read More</span>
  </section>
  <section class="services">
    <h2 class="section-title section-title--light">Our Services</h2>
    <div class="service-cards">
      <article class="service-card">
        <svg class="service-card__icon" viewBox="0 0 50 46" fill="none" stroke="#333" stroke-width="1.3"><circle cx="25" cy="23" r="20" stroke-dasharray="4 3"/><path d="M25 12 L35 17 L35 28 L25 33 L15 28 L15 17Z M15 17 L25 22 L35 17 M25 22 L25 33" stroke="#1565c0"/></svg>
        <h3 class="service-card__title">Blockchain Creation &amp; Launch</h3>
        <ul class="ticks"><li>Base fixed price for cryptocurrency development &amp; launch–would be customizable based on client requirements</li></ul>
      </article>
      <article class="service-card">
        <svg class="service-card__icon" viewBox="0 0 50 46" fill="none" stroke="#333" stroke-width="1.3"><circle cx="25" cy="23" r="7" stroke="#1565c0"/><path d="M4 8 H14 L18 16 M46 8 H36 L32 16 M4 38 H14 L18 30 M46 38 H36 L32 30 M2 23 H18 M32 23 H48"/><circle cx="4" cy="8" r="2"/><circle cx="46" cy="8" r="2"/><circle cx="4" cy="38" r="2"/><circle cx="46" cy="38" r="2"/></svg>
        <h3 class="service-card__title">Basic offering</h3>
        <ul class="ticks"><li>Lower cost per month</li><li>Slower release schedule (about every 3 months)</li><li>Client assists with testing new releases</li><li>Less input into future roadmap/features</li><li>Limited support hours/priority (always available for emergencies)</li></ul>
      </article>
      <article class="service-card">
        <svg class="service-card__icon" viewBox="0 0 50 46" fill="none" stroke="#333" stroke-width="1.3"><rect x="3" y="2" width="20" height="40" rx="3"/><rect x="14" y="12" width="22" height="22" rx="2" stroke="#1565c0"/><path d="M25 16 L31 19 L31 26 L25 29 L19 26 L19 19Z" stroke="#1565c0"/></svg>
        <h3 class="service-card__title">Full service offering</h3>
        <ul class="ticks"><li>Mid-range cost per month</li><li>Releases every 1.5 - 2 months</li><li>Client can help request/prioritize new features</li><li>Full testing by my team prior to release</li><li>Priority support during normal business hours, always available for emergencies</li></ul>
      </article>
    </div>
  </section>
  <section class="offerings">
    <h2 class="section-title">Our Offerings</h2>
    <div class="timeline"></div>
    <div class="offer" style="left:139px"><div class="offer__icon"><svg width="18" height="18" viewBox="0 0 18 18" fill="none" stroke="#fff" stroke-width="1.2"><path d="M9 2 L15 5.5 L15 12.5 L9 16 L3 12.5 L3 5.5Z M3 5.5 L9 9 L15 5.5 M9 9 V16"/></svg></div><div class="offer__dot"></div><div class="offer__label">Blockchain Creation &amp; Launch</div></div>
    <div class="offer" style="left:272px"><div class="offer__icon"><svg width="18" height="18" viewBox="0 0 18 18" fill="none" stroke="#fff" stroke-width="1.2"><rect x="2" y="3" width="14" height="9" rx="1"/><path d="M6 15 H12 M9 12 V15"/></svg></div><div class="offer__dot"></div><div class="offer__label">Blockchain Development</div></div>
    <div class="offer" style="left:399px"><div class="offer__icon"><svg width="18" height="18" viewBox="0 0 18 18" fill="none" stroke="#fff" stroke-width="1.2"><rect x="2" y="2" width="6" height="6"/><rect x="10" y="2" width="6" height="6"/><rect x="2" y="10" width="6" height="6"/><rect x="10" y="10" width="6" height="6"/></svg></div><div class="offer__dot"></div><div class="offer__label">Blockchain Operations</div></div>
    <div class="offer" style="left:511px"><div class="offer__icon"><svg width="18" height="18" viewBox="0 0 18 18" fill="none" stroke="#fff" stroke-width="1.2"><rect x="2" y="2" width="14" height="14" rx="2"/><circle cx="9" cy="10" r="3"/><path d="M2 5 H16"/></svg></div><div class="offer__dot"></div><div class="offer__label">Blockchain Support</div></div>
  </section>
  <section class="why">
    <h2 class="section-title">Why Choose Us</h2>
    <div class="why-cards">
      <article class="why-card"><div class="why-card__icon"><svg width="26" height="22" viewBox="0 0 26 22" fill="none" stroke="#fff" stroke-width="1.3"><path d="M9 3 H17 L20 7 L13 13 L6 7Z"/><path d="M1 16 H7 L13 18 L23 14"/></svg></div><h3 class="why-card__title">VALUE</h3><p class="why-card__text">A team of experts, regular updates, and fixed costs</p></article>
      <article class="why-card why-card--featured"><div class="why-card__icon"><svg width="24" height="24" viewBox="0 0 24 24" fill="none" stroke="#fff" stroke-width="1.3"><circle cx="12" cy="9" r="5"/><path d="M4 22 C4 16 20 16 20 22 M5 9 A7 7 0 0 1 19 9"/></svg></div><h3 class="why-card__title">SUPPORT</h3><p class="why-card__text">Receive advice and other services, beyond development.</p></article>
      <article class="why-card"><div class="why-card__icon"><svg width="20" height="24" viewBox="0 0 20 24" fill="none" stroke="#fff" stroke-width="1.3"><rect x="2" y="2" width="16" height="20" rx="1"/><path d="M6 7 H14 M6 11 H14 M8 15 H12"/></svg></div><h3 class="why-card__title">COMMITMENT</h3><p class="why-card__text">Enjoy regular updates and new features.</p></article>
    </div>
  </section>
  <section class="testimonials">
    <h2 class="section-title">Client Testimonials</h2>
    <div class="quote-cards">
      <article class="quote-card"><span class="quote-card__badge"></span><h3 class="quote-card__name">Lorum Ipsum Dolor</h3><div class="stars">★★★★★</div><p class="quote-card__text">Lorem ipsum dolor sit amet, consectetur adipiscing elit, sed do eiusmod tempor incididunt labore et dolore magna aliquaudet enimad minim veniam quis.</p></article>
      <article class="quote-card"><span class="quote-card__badge"></span><h3 class="quote-card__name">Lorum Ipsum Dolor</h3><div class="stars">★★★★★</div><p class="quote-card__text">Lorem ipsum dolor sit amet, consectetur adipiscing elit, sed do eiusmod tempor incididunt labore et dolore magna aliquaudet enimad minim veniam quis.</p></article>
      <article class="quote-card"><span class="quote-card__badge"></span><h3 class="quote-card__name">Lorum Ipsum Dolor</h3><div class="stars">★★★★★</div><p class="quote-card__text">Lorem ipsum dolor sit amet, consectetur adipiscing elit, sed do eiusmod tempor incididunt labore et dolore magna aliquaudet enimad minim veniam quis.</p></article>
    </div>
  </section>
  <section class="cta">
    <h2 class="section-title section-title--light">Schedule a Free Consultation</h2>
    <p class="cta__text">Lorem ipsum dolor sit amet, consectetur adipiscing elit, sed do eiusmod tempor incididunt ut labore et dolore magna aliqua. Ut enim ad minim veniam, quis nostrud exercitation ullamco laboris nisi ut aliquip ex ea commodo consequat. Duis aute irure dolor in reprehenderit in voluptate velit esse cillum dolore eu fugiat nulla pariatur excepteur.</p>
    <span class="btn cta__btn">Get Started</span>
    <svg class="cta__curve" viewBox="0 0 650 90" preserveAspectRatio="none"><path d="M0,90 Q325,-50 650,90Z" fill="#f4f4f4"/></svg>
  </section>
  <footer class="site-footer">
    <div class="brand"><span class="brand__mark"></span><span class="brand__name">Ledgerwise<br>Forge</span></div>
    <div class="socials"><span></span><span></span><span></span><span></span></div>
    <div class="foot-col foot-col--quick"><h4>Quick Links</h4><ul><li>Home</li><li>About Us</li><li>Our Services</li><li>Our Methods</li><li>Contact Us</li></ul></div>
    <div class="foot-col foot-col--about"><h4>About Links</h4><ul><li>Blog</li><li>Search</li><li>Privacy Policy</li><li>Terms Of Conditions</li></ul></div>
    <div class="foot-col foot-col--news"><h4>Get Our Newsletter</h4><div class="newsletter">Enter Email Address<span class="newsletter__send"><svg width="9" height="9" viewBox="0 0 10 10"><path d="M1 5 L9 1 L6 9 L5 6Z" fill="#fff"/></svg></span></div></div>
    <div class="footer-rule"></div>
    <p class="copyright">Copyrights 2021 LEDGERWISE FORGE. All Rights Reserved</p>
  </footer>
</div>

</div>
</body>
</html>
```